Steadfast Field Crews

We are a underground coal mining labour hire company, needing a website that links into our online payroll (www.wagelinkr.com.au) and also need to have job applications page that is a preform with drop down menu,s with answers or check boxes. We would also need a 3 tier administration access for access to different files.
We are looking for an ongoing relationship with future app integration

Reason: There are a few more designs to come and I'm out at the mine for another week

Industry/Entity Type

Coal Mining

```html
<!DOCTYPE html>
<html lang="en">
<head>
<meta charset="utf-8">
<title>Steadfast Field Crews</title>
<link rel="stylesheet" href="https://fonts.googleapis.com/css2?family=Exo+2:wght@400;600;700&family=Ubuntu:wght@400;500;700&display=swap">
<style>
:root{
  --orange:#f7882f;
  --orange-deep:#e8741c;
  --ink:#000;
  --bar:#121212;
  --band:#262626;
  --tab:#151515;
  --tab-text:#5c5c5c;
  --grey-text:#8c8c8c;
  --white:#fff;
}
*{margin:0;padding:0;box-sizing:border-box}
html,body{width:1200px;height:1029px;overflow:hidden;background:var(--ink)}
body{position:relative;font-family:"Ubuntu",sans-serif;color:var(--white)}
.abs{position:absolute}

/* header */
.site-header{position:absolute;left:0;top:0;width:1200px;height:116px;background:linear-gradient(#1b1a19,#0e0d0c);border-bottom:1px solid #3a3430}
.brand-mark{left:176px;top:26px;width:54px;height:54px;background:var(--orange)}
.brand-name{left:240px;top:28px;font-family:"Exo 2",sans-serif;font-weight:700;font-size:24px;color:var(--white);white-space:nowrap}
.brand-tag{left:241px;top:58px;font-family:"Exo 2",sans-serif;font-weight:700;font-size:11px;color:var(--orange);letter-spacing:.3px;white-space:nowrap}
.social-dot{width:18px;height:18px;border-radius:50%;top:29px;background:#8a8a8a}
.social-dot.active{background:#1e73c9}
.util-link{top:31px;font-family:"Exo 2",sans-serif;font-weight:700;font-size:11px;color:var(--orange);display:flex;align-items:center;gap:5px}
.main-nav{left:0;top:62px;width:1200px;height:40px}
.nav-item{position:absolute;top:0;transform:translateX(-50%);text-align:center;font-size:10.5px;color:#e8e8e8;white-space:nowrap}
.nav-item svg{display:block;margin:0 auto 3px}
.nav-item.current{color:var(--orange)}

/* hero */
.hero{left:0;top:116px;width:1200px;height:401px;background:radial-gradient(ellipse at 35% 45%,#6b4b2e 0%,#3b2c20 40%,#1a1612 100%)}
.hero-shade{left:560px;top:116px;width:640px;height:401px;background:linear-gradient(90deg,rgba(0,0,0,0),rgba(0,0,0,.35))}
.hero-title{left:626px;top:196px;font-family:"Exo 2",sans-serif;font-weight:700;font-size:31px;line-height:39px;color:var(--orange)}
.hero-copy{left:626px;top:282px;width:385px;font-size:20px;line-height:25px;color:#f2f2f2}
.hero-copy b{font-weight:700}
.hero-btn{left:624px;top:402px;width:206px;height:43px;border:1px solid #d8d8d8;background:rgba(0,0,0,.35);display:flex;align-items:center;justify-content:space-between;padding:0 12px 0 14px;font-size:15px}
.slide-dots{left:624px;top:463px;display:flex;gap:2px}
.slide-dots span{width:24px;height:2px;background:#222}
.slide-dots span.on{background:var(--orange)}

/* quick links */
.quick-band{left:0;top:517px;width:1200px;height:98px;background:var(--band)}
.quick-tab{top:547px;width:206px;height:43px;background:var(--tab);border-radius:2px;display:flex;align-items:center;justify-content:center;gap:8px;font-family:"Exo 2",sans-serif;font-weight:700;font-size:15px;color:var(--tab-text)}
.quick-tab.active{border:1px solid var(--orange);color:var(--orange)}
.quick-tab.payroll{color:#e6e6e6;font-family:"Ubuntu",sans-serif;font-weight:500;font-size:22px}

/* welcome */
.welcome-mark{left:800px;top:650px;width:220px;height:220px;border-radius:50%;background:radial-gradient(#2a1c10,#0a0705 70%)}
.welcome-mark-name{left:810px;top:830px;width:200px;text-align:center;font-size:10px;color:#3a3026}
.welcome-title{left:195px;top:652px;width:620px;font-family:"Exo 2",sans-serif;font-weight:700;font-size:31px;line-height:39px;color:var(--orange)}
.welcome-title .lead{color:#b3b3b3}
.welcome-copy{left:195px;top:744px;width:770px;font-size:19px;line-height:24.6px;color:var(--grey-text)}
.welcome-btn{left:195px;top:865px;width:171px;height:38px;border:1px solid var(--orange);display:flex;align-items:center;justify-content:space-between;padding:0 9px 0 10px;font-size:13.5px;color:var(--orange)}

/* footer */
.site-footer{left:0;top:947px;width:1200px;height:82px;background:var(--orange)}
.footer-note{left:186px;top:981px;font-size:13px;color:#1a1a1a;white-space:nowrap}
.footer-dot{top:975px;width:30px;height:30px;border-radius:50%;background:#6c6c6c}
.footer-dot.active{background:#27a6e0}
.footer-dot.light{background:#b9b9b9}
</style>
</head>
<body>

<header class="site-header">
  <div class="abs brand-mark"></div>
  <div class="abs brand-name">Steadfast Field Crews</div>
  <div class="abs brand-tag">FLEXIBLE RESOURCEFUL RELIABLE</div>

  <span class="abs social-dot active" style="left:733px"></span>
  <span class="abs social-dot" style="left:756px"></span>
  <span class="abs social-dot" style="left:779px"></span>
  <span class="abs social-dot" style="left:802px"></span>

  <a class="abs util-link" style="left:847px">
    <svg width="14" height="14" viewBox="0 0 14 14"><path d="M2 1h7v4H7V3H4v8h3V9h2v4H2z M8 6h3V4l3 3-3 3V8H8z" fill="#fff"/></svg>LOGIN</a>
  <a class="abs util-link" style="left:921px">
    <svg width="16" height="14" viewBox="0 0 16 14"><rect x="1" y="5" width="14" height="8" rx="1" fill="none" stroke="#fff" stroke-width="1.4"/><path d="M3 5V2h10v3" fill="none" stroke="#fff" stroke-width="1.4"/></svg>10 20 30 40 50</a>

  <nav class="abs main-nav">
    <div class="nav-item current" style="left:525px"><svg width="13" height="12" viewBox="0 0 13 12"><path d="M6.5 0L13 6h-2v6H8V8H5v4H2V6H0z" fill="#f7882f"/></svg>HOME</div>
    <div class="nav-item" style="left:596px"><svg width="12" height="13" viewBox="0 0 12 13"><rect x="1" y="1" width="10" height="12" fill="none" stroke="#fff" stroke-width="1.4"/><path d="M3 5h6M3 8h6M3 10h4" stroke="#fff"/></svg>APPLICATION</div>
    <div class="nav-item" style="left:680px"><svg width="16" height="13" viewBox="0 0 16 13"><circle cx="6" cy="6" r="5" fill="none" stroke="#fff" stroke-width="1.4"/><circle cx="11" cy="9" r="3.5" fill="#fff"/></svg>PAY PORTAL</div>
    <div class="nav-item" style="left:766px"><svg width="13" height="12" viewBox="0 0 13 12"><path d="M6.5 1L12 11H1z" fill="none" stroke="#fff" stroke-width="1.4"/></svg>INFORMATION <svg style="display:inline;margin:0 0 1px 2px" width="7" height="4" viewBox="0 0 7 4"><path d="M0 0h7L3.5 4z" fill="#fff"/></svg></div>
    <div class="nav-item" style="left:855px"><svg width="13" height="13" viewBox="0 0 13 13"><circle cx="6.5" cy="5" r="3" fill="none" stroke="#fff" stroke-width="1.4"/><path d="M5 9h3v3H5z" fill="#fff"/></svg>ABOUT US</div>
    <div class="nav-item" style="left:930px"><svg width="12" height="13" viewBox="0 0 12 13"><path d="M1 1h10v11H1z" fill="#fff"/><path d="M4 4l4 5" stroke="#111" stroke-width="1.5"/></svg>CONTACT</div>
    <div class="nav-item" style="left:994px"><svg width="13" height="13" viewBox="0 0 13 13"><circle cx="6.5" cy="6.5" r="5.5" fill="none" stroke="#fff" stroke-width="1.4"/><circle cx="6.5" cy="6.5" r="2.2" fill="#fff"/></svg>MISSION</div>
  </nav>
</header>

<section>
  <div class="abs hero" role="img" aria-label="Photo of miners in hard hats and high-visibility gear drilling in an underground rock tunnel"></div>
  <div class="abs hero-shade"></div>
  <svg class="abs" style="left:147px;top:283px" width="38" height="28" viewBox="0 0 38 28">
    <g fill="#f7882f"><circle cx="2" cy="14" r="1.6"/><circle cx="6" cy="10" r="1.6"/><circle cx="6" cy="18" r="1.6"/><circle cx="10" cy="6" r="1.6"/><circle cx="10" cy="22" r="1.6"/><circle cx="14" cy="2" r="1.6"/><circle cx="14" cy="26" r="1.6"/><circle cx="8" cy="14" r="1.6"/><circle cx="14" cy="14" r="1.6"/><circle cx="20" cy="14" r="1.6"/><circle cx="26" cy="14" r="1.6"/><circle cx="32" cy="14" r="1.6"/></g></svg>
  <svg class="abs" style="left:1016px;top:283px" width="38" height="28" viewBox="0 0 38 28">
    <g fill="#9a9a9a"><circle cx="36" cy="14" r="1.6"/><circle cx="32" cy="10" r="1.6"/><circle cx="32" cy="18" r="1.6"/><circle cx="28" cy="6" r="1.6"/><circle cx="28" cy="22" r="1.6"/><circle cx="24" cy="2" r="1.6"/><circle cx="24" cy="26" r="1.6"/><circle cx="30" cy="14" r="1.6"/><circle cx="24" cy="14" r="1.6"/><circle cx="18" cy="14" r="1.6"/><circle cx="12" cy="14" r="1.6"/><circle cx="6" cy="14" r="1.6"/></g></svg>

  <h1 class="abs hero-title">CAREER<br>OPPORTUNITIES</h1>
  <p class="abs hero-copy">Grow your mining career with one of the industry's leaders. Join the <b>SFC</b> team today to see what you've been missing out ......</p>
  <a class="abs hero-btn">Learn more...
    <svg width="26" height="14" viewBox="0 0 26 14"><path d="M1 10c5-6 12-6 18-3M13 1l9 6-9 6M18 2l7 5-7 5" fill="none" stroke="#fff" stroke-width="2"/></svg></a>
  <div class="abs slide-dots"><span></span><span class="on"></span><span></span><span></span></div>
</section>

<section>
  <div class="abs quick-band"></div>
  <a class="abs quick-tab" style="left:183px">Employee Benifit Programs</a>
  <a class="abs quick-tab" style="left:393px">Our Job Vacancies</a>
  <a class="abs quick-tab active" style="left:603px">
    <svg width="22" height="16" viewBox="0 0 22 16"><rect x="1" y="2" width="15" height="12" fill="none" stroke="#f7882f" stroke-width="1.6"/><path d="M4 5h4v4H4zM10 5h3M10 8h3M4 11h9" stroke="#f7882f" stroke-width="1.4" fill="none"/><circle cx="18" cy="12" r="3.5" fill="#f7882f"/></svg>News Letter</a>
  <a class="abs quick-tab payroll" style="left:813px"><span style="width:18px;height:18px;background:#bdbdbd;display:inline-block"></span>wagelinkr</a>
</section>

<section>
  <div class="abs welcome-mark" role="img" aria-label="Faint company emblem decoration"></div>
  <div class="abs welcome-mark-name">Steadfast Field Crews</div>
  <h2 class="abs welcome-title"><span class="lead">WELCOME TO</span> STEADFAST FIELD CREWS</h2>
  <p class="abs welcome-copy">we are experienced in ground consolidation in underground coal mines,&nbsp; in short when they collapse or cave in we come in with chemical pumps and stabilise the ground or fill cavities which will then allow for the mining process to continue. We also do general mine labor as well.</p>
  <a class="abs welcome-btn">LEARN MORE
    <svg width="32" height="14" viewBox="0 0 32 14"><g fill="#f7882f"><circle cx="2" cy="7" r="1.3"/><circle cx="6" cy="7" r="1.3"/><circle cx="10" cy="7" r="1.3"/><circle cx="14" cy="7" r="1.3"/><circle cx="18" cy="7" r="1.3"/><circle cx="22" cy="7" r="1.3"/><circle cx="26" cy="7" r="1.3"/><circle cx="30" cy="7" r="1.3"/><circle cx="26" cy="3" r="1.3"/><circle cx="26" cy="11" r="1.3"/><circle cx="22" cy="1" r="1.3"/><circle cx="22" cy="13" r="1.3"/></g></svg></a>
</section>

<footer>
  <div class="abs site-footer"></div>
  <p class="abs footer-note">©2014&nbsp; Steadfast Field Crews – Underground Construction – Coal Mine Services | Design By Ridgeline Studio.</p>
  <span class="abs footer-dot" style="left:869px"></span>
  <span class="abs footer-dot active" style="left:907px"></span>
  <span class="abs footer-dot" style="left:945px"></span>
  <span class="abs footer-dot light" style="left:983px"></span>
</footer>

</body>
</html>
```